Popular Golf Club needs attractive brochure

We need a brochure that will attract golfers to come to the Kestrel River area and the Brindlewood Golf Club for their golfing holiday. It also needs to address the availability of a function area and corporate functions in the clubhouse and corporate golf days on the course as well.
It will highlight our direct phone contact numbers and website as well.
We are a 36 Hole Championship Golf Course on the Kestrel River border of NSW and Victoria. 3 hours easy freeway drive from Melbourne. Over 300 sunny days every year. Fabulous golf weather all year round. Raincheck guarantee (if it rains we will give you free golf on you next visit).
The area is a golf and watersport playground. Sandy beaches, the mighty Kesterl River, home of the giant Kestrel Perch, fishing, camping, boating and golf all on your doorstep.
We can arrange Golf packages for individuals and groups including 3 and 4 star accommodation available all year round.

Target Market(s)

Golfers looking for holidays

Industry/Entity Type

Accommodation

Requirements
Must have
• Branding bar and logo. Colours signifying sun, grass and river.
Nice to have
• Smiling happy golfers, particularly more senior age group. Map of location and proximity to Melbourne. Photos of the course. some attached, many more available.

```html
<!DOCTYPE html>
<html lang="en">
<head>
<meta charset="utf-8">
<title>Brindlewood Golf Club Brochure</title>
<link href="https://fonts.googleapis.com/css2?family=Open+Sans:wght@400;700&family=Tinos&display=swap" rel="stylesheet">
<style>
:root{
  --bg:#e9e6e1;
  --paper:#ffffff;
  --grass:#8cbd3f;
  --grass-dark:#79aa2f;
  --river:#3aa7c9;
  --sun:#f2c01e;
  --ink:#333333;
  --rule:#9a9a9a;
  --night:#151a12;
}
*{margin:0;padding:0;box-sizing:border-box}
html,body{width:1200px;height:897px;overflow:hidden;background:var(--bg)}
.brochure{
  position:absolute;left:18px;top:32px;width:776px;height:555px;
  transform:scale(1.5);transform-origin:0 0;
  background:var(--paper);overflow:hidden;
  font-family:"Open Sans",Arial,sans-serif;color:var(--ink);
  box-shadow:0 2px 6px rgba(0,0,0,.25);
}
.abs{position:absolute}
.panel-rule{position:absolute;top:0;width:1px;height:450px;background:var(--rule)}
.photo-bar{left:0;top:0;width:259px;height:175px;background:linear-gradient(135deg,#6b4a2a,#c9c4bd 45%,#b48a3c 80%,#8a6a2e)}
.intro{left:17px;top:189px;width:232px;font-size:8.3px;line-height:12.4px}
.intro p{margin-bottom:6px}
.photo-clubhouse{left:260px;top:0;width:257px;height:122px;background:linear-gradient(180deg,#0c0f0a,#26301c 55%,#1d2a12)}
.clubhouse-caption{left:266px;top:80px;font-size:8.8px;line-height:11px;color:#fff;letter-spacing:.4px}
.photo-round{top:145px;width:94px;height:94px;border-radius:50%}
.round-a{left:282px;background:radial-gradient(circle,#c9c2b6,#7a6d5e)}
.round-b{left:396px;background:radial-gradient(circle,#b07a45,#3a2418)}
.url-bar{left:260px;top:254px;width:257px;height:28px;background:var(--grass);color:var(--ink);font-size:13px;text-align:center;line-height:28px}
.map{left:260px;top:282px;width:257px;height:170px;background:linear-gradient(160deg,#ecebe6,#dfe3d6 60%,#cfe0c6)}
.photo-golfers{left:518px;top:0;width:258px;height:193px;background:linear-gradient(180deg,#c8d8b0,#9fbf6a 45%,#7fa94a)}
.tagline{left:518px;top:210px;width:258px;text-align:center;font-family:"Tinos","Times New Roman",serif;font-size:10.5px;letter-spacing:.2px}
.club-mark{left:548px;top:282px;display:flex;align-items:center;gap:8px}
.club-dot{width:44px;height:44px;border-radius:50%;background:var(--grass)}
.club-name{font-size:14px;letter-spacing:3.5px;line-height:17px;color:#555}
.swoosh{left:0;top:0;width:776px;height:555px}
.foot{color:#fff;text-align:center}
.foot-url-left{left:40px;top:490px;font-size:13px}
.foot-address{left:270px;top:467px;width:236px;font-size:8.3px;line-height:19px}
.foot-address b{font-weight:700}
.foot-call{left:540px;top:462px;width:228px}
.call-head{font-size:17px;font-weight:700;letter-spacing:.5px}
.call-num{font-size:18px;margin-top:4px}
.call-url{font-size:13.5px;margin-top:3px}
</style>
</head>
<body>
<div class="brochure">
  <div class="abs photo-bar" role="img" aria-label="Photo of beer taps at the clubhouse bar"></div>
  <div class="abs intro">
    <p>The secret is out! Along the Mighty Kestrel<br>Brindlewood Golf Course is maintained at the highest levels of excellence unsurpassed on the River.<br>This magnificent 36 hole championship sand-belt course offers a challenge to golfers of all levels and hosts the annual Southern Pro Trainee Championships.</p>
    <p>Within excess of 300 days of sunshine each year the regionboasts more sunny weather than the Gold Coast with two superb golf courses (President's and Captain's) that are suitable to play all year round.</p>
    <p>The courses abound with our native flora and fauna and water features are home to an amazing abundance of bird life. Kangaroos regularly frequent the lush fairways to graze and laze in the shade during the warmth of the after noon sun</p>
  </div>

  <div class="abs photo-clubhouse" role="img" aria-label="Night photo of the lit clubhouse across the course"></div>
  <div class="abs clubhouse-caption">36 Championship holes<br>Modern clubhouse and meals everyday!<br>Come play a round at your friendly Club</div>
  <div class="abs photo-round round-a" role="img" aria-label="Photo of members seated at a clubhouse table"></div>
  <div class="abs photo-round round-b" role="img" aria-label="Photo of a busy function in the clubhouse"></div>
  <div class="abs url-bar">www.brindlewoodgolf.com.au</div>
  <div class="abs map" role="img" aria-label="Street map showing the club location in town"></div>

  <div class="abs photo-golfers" role="img" aria-label="Photo of four smiling golfers on the green"></div>
  <div class="abs tagline">"A great golf course is just the beginning..."</div>
  <div class="abs club-mark">
    <div class="club-dot"></div>
    <div class="club-name">BRINDLEWOOD<br>GOLF CLUB</div>
  </div>

  <div class="panel-rule" style="left:259px"></div>
  <div class="panel-rule" style="left:517px"></div>

  <svg class="abs swoosh" viewBox="0 0 776 555" aria-hidden="true">
    <path d="M0 452 Q380 432 776 420 L776 555 L0 555 Z" fill="var(--grass)"/>
    <path d="M0 450 Q380 430 776 413 L776 420 Q380 437 0 457 Z" fill="#ffffff"/>
    <path d="M0 442 Q360 432 776 404 L776 412 Q370 440 0 449 Z" fill="var(--sun)"/>
    <path d="M0 404 Q200 428 380 443 Q600 440 776 416 L776 421 Q600 446 380 450 Q190 436 0 412 Z" fill="var(--river)"/>
  </svg>

  <div class="abs foot foot-url-left">www.brindlewoodgolf.com.au</div>
  <div class="abs foot foot-address">
    <b>Brindlewood Golf Club</b><br>
    Wattle Road, PO Box 48, Brindlewood NSW 2799<br>
    P: 03 5550 1234 &nbsp;|&nbsp; F: 03 5550 1235<br>
    <b>FREECALL:</b> 1800 555 019
  </div>
  <div class="abs foot foot-call">
    <div class="call-head">CALL US TODAY</div>
    <div class="call-num">03 5550 1234</div>
    <div class="call-url">www.brindlewoodgolf.com.au</div>
  </div>
</div>
</body>
</html>
```